VOMRA Pty Ltd Business Card

Looking for a simple yet eye-catching double-sided business card design using my company logo on one side and contact details on the other.

Target Market(s)

Government

Industry/Entity Type

Communication Systems Engineering

Contact Information for Business Card

VOMRA Pty Ltd

Requirements
Nice to have
• Would be great to have a QR code so details can be scanned into contacts

```html
<!DOCTYPE html>
<html lang="en">
<head>
<meta charset="utf-8">
<title>VOMRA Pty Ltd Business Card</title>
<link href="https://fonts.googleapis.com/css2?family=Open+Sans:wght@400;700&display=swap" rel="stylesheet">
<style>
  :root {
    --backdrop: #232323;
    --card: #37424a;
    --ink: #ffffff;
    --card-shadow: rgba(0, 0, 0, 0.55);
  }
  * { margin: 0; padding: 0; box-sizing: border-box; }
  html, body {
    width: 1200px;
    height: 780px;
    overflow: hidden;
    background: var(--backdrop);
    font-family: "Open Sans", sans-serif;
    color: var(--ink);
  }
  .canvas {
    position: relative;
    width: 1200px;
    height: 780px;
  }
  .card {
    position: absolute;
    top: 110px;
    width: 340px;
    height: 560px;
    background: var(--card);
    box-shadow: 0 14px 30px var(--card-shadow);
    overflow: hidden;
  }
  .card--front {
    left: 225px;
    border-radius: 150px 0 150px 0;
  }
  .card--back {
    left: 635px;
    border-radius: 0 150px 0 150px;
  }

  /* Front: brand name set large, reading upward */
  .front-name {
    position: absolute;
    left: 170px;
    top: 195px;
    transform: translate(-50%, -50%) rotate(-90deg);
    font-weight: 700;
    font-size: 70px;
    letter-spacing: 4px;
    line-height: 1;
    white-space: nowrap;
  }
  .front-mark {
    position: absolute;
    left: 120px;
    top: 375px;
    width: 100px;
    height: 100px;
    border-radius: 50%;
    border: 3px solid var(--ink);
  }

  /* Back: brand line and contact block */
  .brand {
    position: absolute;
    top: 62px;
    left: 0;
    right: 0;
    display: flex;
    align-items: center;
    justify-content: center;
    gap: 16px;
  }
  .brand-mark {
    width: 46px;
    height: 46px;
    border-radius: 50%;
    border: 2px solid var(--ink);
  }
  .brand-name {
    font-weight: 700;
    font-size: 40px;
    letter-spacing: 4px;
    line-height: 1;
  }
  .contact {
    position: absolute;
    top: 260px;
    left: 0;
    right: 0;
    text-align: center;
  }
  .person-name {
    font-weight: 700;
    font-size: 24px;
    line-height: 1.2;
  }
  .person-role {
    font-size: 14px;
    margin-bottom: 14px;
  }
  .contact-icons {
    display: flex;
    justify-content: center;
    gap: 8px;
    margin-bottom: 6px;
  }
  .icon {
    width: 24px;
    height: 24px;
  }
  .contact-lines {
    font-size: 14px;
    line-height: 1.4;
    margin-bottom: 14px;
  }
  .address {
    font-size: 14px;
    line-height: 1.4;
    margin-top: 8px;
  }
</style>
</head>
<body>
<main class="canvas">

  <section class="card card--front" aria-label="Card front">
    <div class="front-name">VOMRA</div>
    <div class="front-mark" aria-hidden="true"></div>
  </section>

  <section class="card card--back" aria-label="Card back">
    <div class="brand">
      <div class="brand-mark" aria-hidden="true"></div>
      <div class="brand-name">VOMRA</div>
    </div>

    <div class="contact">
      <p class="person-name">Daniel Whitcombe</p>
      <p class="person-role">Co-Founder</p>

      <div class="contact-icons">
        <svg class="icon" viewBox="0 0 24 24" aria-label="Phone">
          <circle cx="12" cy="12" r="12" fill="#ffffff"/>
          <path d="M8.5 6.5l2 2.2-1.2 1.5c.8 1.7 2 2.9 3.6 3.7l1.5-1.2 2.2 2-1.3 2c-4.6-.4-8.4-4.2-8.8-8.8z" fill="#37424a"/>
        </svg>
        <svg class="icon" viewBox="0 0 24 24" aria-label="Email">
          <circle cx="12" cy="12" r="12" fill="#ffffff"/>
          <rect x="6" y="8" width="12" height="8.5" rx="1" fill="none" stroke="#37424a" stroke-width="1.6"/>
          <path d="M6.5 8.6L12 12.8l5.5-4.2" fill="none" stroke="#37424a" stroke-width="1.6"/>
        </svg>
        <svg class="icon" viewBox="0 0 24 24" aria-label="Website">
          <circle cx="12" cy="12" r="12" fill="#ffffff"/>
          <circle cx="12" cy="12" r="6" fill="none" stroke="#37424a" stroke-width="1.5"/>
          <ellipse cx="12" cy="12" rx="2.6" ry="6" fill="none" stroke="#37424a" stroke-width="1.3"/>
          <path d="M6 12h12" stroke="#37424a" stroke-width="1.3"/>
        </svg>
      </div>

      <div class="contact-lines">
        <p>(02) 5550-1487</p>
        <p>www.vomra.com.au</p>
        <p>admin@vomra.com.au</p>
      </div>

      <svg class="icon" viewBox="0 0 24 24" aria-label="Location">
        <circle cx="12" cy="12" r="12" fill="#ffffff"/>
        <path d="M12 5.5a4.3 4.3 0 0 0-4.3 4.3c0 3.2 4.3 8 4.3 8s4.3-4.8 4.3-8A4.3 4.3 0 0 0 12 5.5z" fill="#37424a"/>
        <circle cx="12" cy="9.8" r="1.6" fill="#ffffff"/>
      </svg>
      <div class="address">
        <p>14-16 Harbour Lane Redfern</p>
        <p>NSW 2016 Australia</p>
      </div>
    </div>
  </section>

</main>
</body>
</html>
```